New letter head for Air Conditioning business

We need a new professional letter head design to suit our new re-branded air conditioning business. Our new logo is attached

```html
<!DOCTYPE html>
<html lang="en">
<head>
<meta charset="utf-8">
<title>Nortavo Letterhead</title>
<link href="https://fonts.googleapis.com/css2?family=Roboto:wght@400;500;700&display=swap" rel="stylesheet">
<style>
  :root {
    --backdrop: #e4e4e4;
    --paper: #fbfbfb;
    --ink-dark: #333333;
    --ink-body: #8c8c8c;
    --ink-meta: #7a7a7a;
    --brand-green: #3caa72;
    --brand-red: #e2695a;
    --signature-blue: #1f77b8;
    --band-dark: #2f2f2f;
  }
  * { box-sizing: border-box; margin: 0; padding: 0; }
  html, body {
    width: 1200px; height: 1001px; overflow: hidden;
    background: var(--backdrop);
    font-family: "Roboto", Arial, sans-serif;
  }
  .letterhead {
    position: absolute; left: 260px; top: 20px;
    width: 679px; height: 960px;
    background: var(--paper);
    box-shadow: 0 6px 24px rgba(0,0,0,0.12);
    overflow: hidden;
  }
  .brand { position: absolute; left: 45px; top: 120px; }
  .brand-name {
    font-weight: 700; font-size: 35px; letter-spacing: 5px;
    color: var(--ink-dark); line-height: 1;
  }
  .brand-tagline {
    margin-top: 7px; font-size: 7.4px; font-weight: 500;
    letter-spacing: 1.6px; color: var(--brand-green);
  }
  .edge-tab {
    position: absolute; width: 13px;
    background: linear-gradient(to bottom, var(--brand-red), var(--brand-green));
  }
  .edge-tab.right { right: 0; top: 52px; height: 108px; border-radius: 12px 0 0 12px; }
  .edge-tab.left { left: 0; top: 870px; height: 62px; border-radius: 0 12px 12px 0; }
  .meta { position: absolute; top: 241px; font-size: 10.5px; color: var(--ink-meta); }
  .meta.salutation { left: 45px; }
  .meta.date { right: 46px; }
  .subject {
    position: absolute; left: 86px; top: 268px; width: 134px;
    font-size: 10.5px; line-height: 17px; color: var(--ink-body);
  }
  .body-copy { position: absolute; left: 45px; top: 356px; width: 588px; }
  .body-copy p {
    font-size: 10.9px; line-height: 17px; color: var(--ink-body);
    text-align: justify; text-indent: 21px; margin-bottom: 17px;
  }
  .sign-off { position: absolute; left: 45px; top: 684px; }
  .sign-label { font-size: 10.5px; font-weight: 500; color: var(--ink-meta); }
  .signature {
    margin-top: 6px; width: 156px; height: 34px; border-radius: 4px;
    background: linear-gradient(90deg, rgba(31,119,184,0.25), rgba(31,119,184,0.08));
  }
  .sign-role { margin-top: 16px; font-size: 10.5px; color: var(--ink-meta); }
  .contact {
    position: absolute; top: 892px; display: flex; gap: 7px;
    font-size: 11px; line-height: 15px; color: var(--ink-dark);
  }
  .contact .icons { display: flex; flex-direction: column; gap: 4px; padding-top: 2px; }
  .contact svg { width: 10px; height: 10px; display: block; }
  .contact.phones { left: 45px; }
  .contact.online { left: 169px; }
  .contact.address { left: 351px; }
  .footer-brand {
    position: absolute; right: 46px; top: 893px;
    font-size: 14px; font-weight: 700; letter-spacing: 1.5px; color: var(--ink-dark);
  }
  .footer-band {
    position: absolute; right: 0; bottom: 0; width: 238px; height: 16px;
    background: var(--band-dark);
    clip-path: polygon(16px 0, 100% 0, 100% 100%, 0 100%);
  }
</style>
</head>
<body>
  <main class="letterhead">
    <div class="edge-tab right"></div>

    <header class="brand">
      <div class="brand-name">NORTAVO</div>
      <div class="brand-tagline">AIR CONDITIONING &amp; REFRIGERATION</div>
    </header>

    <div class="meta salutation">Dear Sir,</div>
    <div class="meta date">Dated: 00/00/0000</div>

    <div class="subject">Lorem Ipsum is simply dummy text of the printing and typesetting industry.</div>

    <section class="body-copy">
      <p>Lorem Ipsum is simply dummy text of the printing and typesetting industry. Lorem Ipsum has been the industry's standard dummy text ever since the 1500s, when an unknown printer took a galley of type and scrambled it to make a type specimen book. It has survived not only five centuries, but also the leap into electronic typesetting, remaining essentially unchanged. It was popularised in the 1960s with the release of Veltrand sheets containing Lorem Ipsum passages, and more recently with desktop publishing software like Orvin LayoutDesk including versions of Lorem Ipsum.</p>
      <p>Lorem Ipsum is simply dummy text of the printing and typesetting industry. Lorem Ipsum has been the industry's standard dummy text ever since the 1500s, when an unknown printer took a galley of type and scrambled it to make a type specimen book. It has survived not only five centuries, but also the leap into electronic typesetting, remaining essentially unchanged. It was popularised in the 1960s with the release of Veltrand sheets containing Lorem Ipsum passages, and more recently with desktop publishing software like Orvin LayoutDesk including versions of Lorem Ipsum.</p>
      <p>Lorem Ipsum is simply dummy text of the printing and typesetting industry. Lorem Ipsum has been the industry's standard dummy text ever since the 1500s, when an unknown printer took a galley of type and scrambled it to make a type specimen book.</p>
    </section>

    <section class="sign-off">
      <div class="sign-label">Your Name</div>
      <div class="signature" role="img" aria-label="Handwritten signature of Marcus Ellery"></div>
      <div class="sign-role">CEO &nbsp;|&nbsp; Owner</div>
    </section>

    <div class="edge-tab left"></div>

    <footer>
      <div class="contact phones">
        <div class="icons">
          <svg viewBox="0 0 10 10"><path d="M1 4c0-2 8-2 8 0v1H7V4H3v1H1z M2 6h6l1 3H1z" fill="var(--brand-green)"/></svg>
          <svg viewBox="0 0 10 10"><rect x="3" y="1" width="4" height="3" fill="var(--brand-green)"/><rect x="1" y="4" width="8" height="4" rx="1" fill="var(--brand-green)"/><rect x="3" y="7" width="4" height="2" fill="#fff" stroke="var(--brand-green)" stroke-width="0.8"/></svg>
        </div>
        <div>(000) 000-0000<br>(222) 222-2222</div>
      </div>
      <div class="contact online">
        <div class="icons">
          <svg viewBox="0 0 10 10"><rect x="1" y="2" width="8" height="6" fill="var(--brand-red)"/><path d="M1 2l4 3.5L9 2" fill="none" stroke="#fff" stroke-width="0.9"/></svg>
          <svg viewBox="0 0 10 10"><circle cx="5" cy="5" r="3.8" fill="none" stroke="var(--brand-red)" stroke-width="1.1"/><path d="M1.2 5h7.6M5 1.2c-2 2.5-2 5.1 0 7.6M5 1.2c2 2.5 2 5.1 0 7.6" fill="none" stroke="var(--brand-red)" stroke-width="0.8"/></svg>
        </div>
        <div>info@nortavocooling.com<br>www.nortavocooling.com</div>
      </div>
      <div class="contact address">
        <div class="icons">
          <svg viewBox="0 0 10 10"><path d="M5 9.5C2.5 6.5 1.8 5 1.8 3.9a3.2 3.2 0 0 1 6.4 0C8.2 5 7.5 6.5 5 9.5z" fill="var(--brand-green)"/><circle cx="5" cy="3.9" r="1.2" fill="#fff"/></svg>
        </div>
        <div>4180 Larkspur Avenue, Fairhaven,<br>Other ABC 55555</div>
      </div>
      <div class="footer-brand">NORTAVO</div>
      <div class="footer-band"></div>
    </footer>
  </main>
</body>
</html>
```